2 x Digitize Logo | 2 x Business Cards | 2 x Fridge Magnets

We require 6 deliverables:
1. Residential logo redrawn (same just high quality for large print format).
2. Corporate logo redrawn (minor changes to wording and high quality for large print format).
3. New business card design for Furniture Removals (residential)
4. New business card design for Corporate Relocations (business)
5. New Fridge magnet for Furniture removals (residential)
6. New fridge magnet for Corporate Relocations (business)
1. Residential Logo
a. We require the logo to be translated into a high quality digital image with no modifications.
(see attached resilogo.jpg)
2. Residential Logo
a. We require the logo to be edited (add the word corporate relocations) be translated into a high quality digital image.
(see attached corplogo.jpg)
3. Using the resilogo please make a new business card for our business.
a. Please see the web site https://www.larkbendcarters.com.au for colours and inspiration.
b. The residential business card needs the following information:
i. Business Name (using the residential logo).
ii. Free Call: 1800 LB Cart (the L, B and Cart much be the same colour as the logo).
iii. Website: www.LarkbendCarters.com.au
iv. Address: 4/17 Ormsdale Court, VIC 3264
v. Email: cart@LarkbendCarters.com.au
vi. backof Card:
Review our service
www.PennantOrbit.com.au
Services: Local, Country, Interstate | Furniture Removals | Piano, Billiard Tables & Antiques
4. Using the corplogo please make a new business card for our business.
b. The corporate business card needs the following information:
i. Business Name (using the corporate logo).
v. Email: corporate@LarkbendCarters.com.au
vi. Back of Card:
Review our service
www.PennantOrbit.com.au
Services: Corporate relocations | Office equipment moves | Packing Service | Packing Materials
5. Using the resilogo please make a new fridge magent for our business.
b. The residential fidge magnet needs the following information:
iv. Services: Local, Country, Interstate | Furniture Removals | Piano, Billiard Tables & Antiques
6. Using the corplogo please make a new fridge magent for our business.
b. The corporate fidge magnet needs the following information:
iv. Services: Local, Country, Interstate | Corporate relocations
Target Market(s)
Residential Furniture Removals and Corporate Office relocations
Industry/Entity Type
Business
Contact Information for Business Card
Please see full brief for six items required
Requirements
Must have
- Clean simple, easy to read
Nice to have
- fresh, stand out, eye catching
Should not have
- plain, standard, boring, general

```html
<!DOCTYPE html>
<html lang="en">
<head>
<meta charset="utf-8">
<title>Larkbend Carters – Business Card</title>
<link rel="stylesheet" href="https://fonts.googleapis.com/css2?family=Source+Sans+3:ital,wght@0,400;0,700;1,400&display=swap">
<style>
  :root {
    --backdrop: #313131;
    --card-white: #ffffff;
    --brand-green: #24b24d;
    --brand-red: #ec1c24;
    --brand-yellow: #fdc90f;
    --ink-light: #ffffff;
  }
  * { box-sizing: border-box; margin: 0; padding: 0; }
  html, body {
    width: 1200px; height: 900px; overflow: hidden;
    background: var(--backdrop);
    font-family: "Source Sans 3", "Myriad Pro", Arial, sans-serif;
    color: var(--ink-light);
  }
  .stage { position: relative; width: 1200px; height: 900px; }
  .card {
    position: absolute; top: 306px; width: 440px; height: 271px;
    border-radius: 10px; overflow: hidden;
    display: flex; flex-direction: column;
    box-shadow: 0 2px 6px rgba(0,0,0,0.35);
  }
  .card--front { left: 149px; background: var(--card-white); }
  .card--back { left: 608px; height: 272px; }
  .band {
    display: flex; flex-direction: column; align-items: center; justify-content: center;
    text-align: center; font-size: 15px; line-height: 20px;
  }
  .band--white { background: var(--card-white); }
  .band--green { background: var(--brand-green); }
  .band--red { background: var(--brand-red); }
  .band--yellow { background: var(--brand-yellow); }
  .wordmark {
    font-weight: 700; font-size: 30px; letter-spacing: 0.5px;
    text-transform: uppercase; line-height: 1;
  }
  .wordmark--green { color: var(--brand-green); }
  .wordmark--white { color: var(--ink-light); }
  .review-label { font-style: italic; font-size: 15px; line-height: 20px; }
  .review-url { font-size: 20px; line-height: 26px; }
  .services { font-size: 15px; line-height: 20px; text-transform: uppercase; }
</style>
</head>
<body>
<main class="stage">
  <section class="card card--front" aria-label="Card front">
    <div class="band band--white" style="height:100px"><span class="wordmark wordmark--green">Larkbend Carters</span></div>
    <div class="band band--green" style="height:52px">
      <p>1800 LB Cart</p>
      <p>cart@LarkbendCarters.com.au</p>
    </div>
    <div class="band band--red" style="height:52px"><p>4/17 Ormsdale Court, VIC 3264</p></div>
    <div class="band band--yellow" style="height:53px"><p>www.LarkbendCarters.com.au</p></div>
    <div class="band band--white" style="flex:1"></div>
  </section>

  <section class="card card--back" aria-label="Card back">
    <div class="band band--green" style="height:90px"><span class="wordmark wordmark--white">Larkbend Carters</span></div>
    <div class="band band--red" style="height:93px">
      <p class="review-label">Review our service</p>
      <p class="review-url">www.PennantOrbit.com.au</p>
    </div>
    <div class="band band--yellow services" style="flex:1">
      <p>Local, Country, Interstate</p>
      <p>Furniture Removals</p>
      <p>Piano, Billiard Tables &amp; Antiques</p>
    </div>
  </section>
</main>
</body>
</html>
```